Laser Tattoo Removal Business Cards

We are looking for a professional business card design for a laser tattoo removal business. Ideally looking for a black business card design. The name of the business is Brightline Tattoo Removal. We place our cards at local tattoo shops so we ideally are looking for something trendy/edgy to draw both male and female clientele in.

Target Market(s)

Male/Female ages 18-60

Contact Information for Business Card

black background ideally.. hoping to stay within greys, whites and black

Font styles to use
Serif
Sans Serif

Colors
121212
a9a9a9
5c5c5c
f5f5f5
ffffff
7f7f7f
606060
848484
9d9d9d

Requirements
Must have
• Employee Info:
• Melissa Thornbury
• Chief Executive Offer
• m: 919.537.2846
• w: 919.362.4178
• f: 919.685.3907
• mthornbury@brightlinetattooremoval.example
• Address:
• 4615 Oakmere Pkwy, Suite 210
• Raleigh, NC 27654
• Website:
• www.brightlinetattooremoval.example
Nice to have
• Myabe business name on back or logo on back and employee info on the front

```html
<!DOCTYPE html>
<html lang="en">
<head>
<meta charset="utf-8">
<title>Brightline Tattoo Removal – Business Cards</title>
<link href="https://fonts.googleapis.com/css2?family=Roboto:wght@400;500;700&display=swap" rel="stylesheet">
<style>
  :root {
    --page-bg: #e9e9e9;
    --card-front-dark: #2a2a2a;
    --card-back: #121212;
    --paper: #f5f5f5;
    --ink-light: #ffffff;
    --ink-dark: #2a2a2a;
  }
  html, body {
    margin: 0;
    padding: 0;
    width: 1200px;
    height: 960px;
    overflow: hidden;
    background: var(--page-bg);
    font-family: "Roboto", Arial, sans-serif;
  }
  .canvas {
    position: relative;
    width: 1200px;
    height: 960px;
  }
  .card {
    position: absolute;
    width: 600px;
    height: 343px;
    overflow: hidden;
  }
  .card-front {
    left: 322px;
    top: 108px;
    background: var(--card-front-dark);
  }
  .card-back {
    left: 320px;
    top: 493px;
    height: 344px;
    background: var(--card-back);
  }
  .front-curve {
    position: absolute;
    inset: 0;
  }
  .contact {
    position: absolute;
    left: 25px;
    top: 78px;
    color: var(--ink-light);
    font-size: 14px;
    line-height: 19px;
  }
  .contact-name {
    margin: 0;
    font-size: 20px;
    font-weight: 500;
    line-height: 24px;
    letter-spacing: 0.2px;
  }
  .contact-title {
    margin: 0 0 11px;
    font-size: 14.5px;
    font-weight: 500;
  }
  .contact-address,
  .contact-lines {
    margin: 0 0 8px;
    font-style: normal;
  }
  .contact-lines .small {
    font-size: 12.5px;
  }
  .brand-name {
    position: absolute;
    margin: 0;
    text-align: center;
    text-transform: uppercase;
    font-weight: 500;
    font-size: 26px;
    line-height: 36px;
    letter-spacing: 3px;
  }
  .card-front .brand-name {
    left: 300px;
    right: 0;
    top: 134px;
    color: var(--ink-dark);
  }
  .card-back .brand-name {
    left: 0;
    right: 0;
    top: 136px;
    font-size: 32px;
    line-height: 42px;
    color: var(--ink-light);
  }
</style>
</head>
<body>
<main class="canvas">
  <section class="card card-front" aria-label="Business card front">
    <svg class="front-curve" width="600" height="343" viewBox="0 0 600 343" aria-hidden="true">
      <path d="M318 0 C 250 95, 258 258, 318 343 L600 343 L600 0 Z" fill="var(--paper)"/>
    </svg>
    <div class="contact">
      <p class="contact-name">MELISSA THORNBURY</p>
      <p class="contact-title">Chief Executive Offer</p>
      <address class="contact-address">4615 Oakmere Pkwy, Suite 210<br>Raleigh, NC 27654</address>
      <p class="contact-lines">
        (W) 919.362.4178<br>
        (M) 919.537.2846<br>
        (F) 919.685.3907<br>
        <span class="small">mthornbury@brightlinetattooremoval.example</span><br>
        <span class="small">www.brightlinetattooremoval.example</span>
      </p>
    </div>
    <p class="brand-name">Brightline<br>Tattoo Removal</p>
  </section>

  <section class="card card-back" aria-label="Business card back">
    <p class="brand-name">Brightline<br>Tattoo Removal</p>
  </section>
</main>
</body>
</html>
```